Flat bootstrap design for existing site

I'm looking for a modern flat design based around an existing logo. This has to be a custom design (no external templates), and implemented into a bootstrap framework.

The logo is attached as 2 versions - choose whichever you want, that flows better with whatever design you choose.

Added screenshots of the existing site (currently using the default bootstrap layouts). Please make your designs around those pages in the screenshots (i.e. the homepage only has the postal code input and the header). The active page has 3 screenshots, because I wanted to illustrate the other states that would be visible (in the table rows).

This is a moving/junk removal website, just for some context.

Here's some example websites (flat designs) that I like, just to give you an idea of what I'm after.

https://www.plimvora.com/
https://dacklow.com/
https://trevanu.com/
https://quobrintal.com/en/

Coding

Coded - Design and coding required

Number of Pages Required

5+ page

Colors

Designer to choose colors to be used in the design.

Requirements
Must have
• It must be a modern/simple flat design, that is built around the existing logo (attached).
• It has to be implemented using bootstrap.

```html
<!DOCTYPE html>
<html lang="en">
<head>
<meta charset="utf-8">
<title>Booking Details</title>
<link href="https://fonts.googleapis.com/css2?family=Mulish:wght@400;600;700;800&display=swap" rel="stylesheet">
<style>
:root{
  --sky:#3fc3f2;
  --sky-deep:#1fb0ec;
  --header:#0aaeeb;
  --title:#2b86c9;
  --note:#4cc0ec;
  --ink:#333;
  --line:#e2e2e2;
  --field:#bdbdbd;
  --btn:#46c3f0;
  --accept:#33c97a;
  --sent:#6fc1e6;
  --pending:#777;
  --row:#f7f7f7;
}
*{box-sizing:border-box;margin:0;padding:0}
html,body{width:1200px;height:1194px;overflow:hidden}
body{
  position:relative;
  font-family:"Mulish",sans-serif;
  color:var(--ink);
  background:linear-gradient(135deg,#5fd0f6 0%,var(--sky) 45%,var(--sky-deep) 100%);
}
.site-header{
  position:absolute;left:0;top:0;width:1200px;height:108px;
  background:linear-gradient(90deg,#14b6ee,var(--header));
}
.brand{
  position:absolute;left:86px;top:34px;
  display:flex;align-items:center;gap:10px;
  color:#fff;font-weight:800;font-size:34px;letter-spacing:1px;
}
.brand-dot{width:16px;height:16px;border-radius:50%;background:#fff}
.main-nav{position:absolute;top:40px;left:0;width:1200px;height:20px;font-size:16px;color:#fff}
.main-nav span{position:absolute;white-space:nowrap}
.caret{display:inline-block;margin-left:5px;border-left:5px solid transparent;border-right:5px solid transparent;border-top:6px solid #fff;vertical-align:2px}
.card{position:absolute;background:#fff;border-radius:6px}
.card-title{position:absolute;left:0;width:100%;text-align:center;color:var(--title);font-size:28px;font-weight:400;letter-spacing:.5px}
.card hr{position:absolute;left:81px;width:867px;border:0;border-top:1px solid var(--line)}
.booking{left:89px;top:155px;width:1023px;height:424px}
.label{position:absolute;font-size:18px;font-weight:600;color:#333}
.field{
  position:absolute;height:49px;border:1px solid var(--field);border-radius:25px;
  box-shadow:0 2px 3px rgba(0,0,0,.12);
  display:flex;align-items:center;padding:0 20px;font-size:15px;color:#555;
}
.field svg{position:absolute;right:20px;top:50%;transform:translateY(-50%)}
.update-btn{
  position:absolute;left:427px;top:330px;width:168px;height:53px;border-radius:27px;
  background:var(--btn);color:#fff;font-size:21px;display:flex;align-items:center;justify-content:center;
  box-shadow:0 4px 8px rgba(0,0,0,.18);letter-spacing:.5px;
}
.drivers{left:87px;top:606px;width:1023px;height:518px}
.drivers hr{left:81px;width:866px}
.note{position:absolute;left:0;top:104px;width:100%;text-align:center;color:var(--note);font-size:17px}
.driver-table{position:absolute;left:83px;top:159px;width:868px;height:312px;border:1px solid #aaa;background:var(--row)}
.tr{position:absolute;left:0;width:100%;border-bottom:1px solid #ddd;font-size:14px}
.tr span{position:absolute;top:50%;transform:translateY(-50%);white-space:nowrap}
.th{font-size:16px}
.badge{width:123px;height:26px;border-radius:13px;color:#fff;font-size:13.5px;display:flex;align-items:center;justify-content:center;box-shadow:0 2px 3px rgba(0,0,0,.15)}
.badge.accepted{background:var(--accept)}
.badge.sent{background:var(--sent)}
.badge.pending{background:var(--pending)}
.paid{color:#666;font-size:13px}
</style>
</head>
<body>
<header class="site-header">
  <div class="brand"><span class="brand-dot"></span>HAULVANE</div>
  <nav class="main-nav">
    <span style="left:487px">BOOK</span>
    <span style="left:584px">HOW IT WORKS</span>
    <span style="left:759px">BECOME A DRIVER</span>
    <span style="left:954px">sam@mailvento.com<i class="caret"></i></span>
  </nav>
</header>

<section class="card booking">
  <h1 class="card-title" style="top:30px">BOOKING DETAILS</h1>
  <hr style="top:85px">
  <div class="label" style="left:81px;top:122px">Package selected:</div>
  <div class="field" style="left:79px;top:153px;width:412px">Package 1
    <svg width="12" height="16" viewBox="0 0 12 16"><path d="M6 1l5 6H1zM6 15l5-6H1z" fill="#555"/></svg>
  </div>
  <div class="label" style="left:537px;top:122px">Pick-up time selected:</div>
  <div class="field" style="left:535px;top:153px;width:412px">July18 at 4.13 am
    <svg width="17" height="17" viewBox="0 0 17 17"><rect x="1" y="3" width="15" height="13" fill="none" stroke="#555" stroke-width="1.5"/><path d="M1 7h15M5 1v4M12 1v4M5 10h1M8 10h1M11 10h1M5 13h1M8 13h1M11 13h1" stroke="#555" stroke-width="1.5"/></svg>
  </div>
  <div class="label" style="left:81px;top:223px">Description:</div>
  <div class="field" style="left:79px;top:255px;width:867px">1 large stove</div>
  <div class="update-btn">UPDATE</div>
</section>

<section class="card drivers">
  <h2 class="card-title" style="top:30px">DRIVERS IN YOUR AREA</h2>
  <hr style="top:81px">
  <p class="note">Please stay on this pade and be patient, while we contact drivers and find you one ASP.</p>
  <div class="driver-table">
    <div class="tr th" style="top:0;height:54px"><span style="left:25px">Name</span><span style="left:168px">Distance(km)</span><span style="left:355px">Agreed pick-up time</span></div>
    <div class="tr" style="top:54px;height:61px"><span style="left:25px">Owen Marsh</span><span style="left:168px">4.00km awry</span><span style="left:355px">July18 at 4.13 am</span><span class="badge accepted" style="left:559px">Time Accepted</span><span class="paid" style="left:738px">Payment Made</span></div>
    <div class="tr" style="top:115px;height:60px"><span style="left:25px">Peter Lang</span><span style="left:170px">5.7km away</span><span style="left:408px">_</span><span class="badge sent" style="left:559px">Request Sent</span></div>
    <div class="tr" style="top:175px;height:66px"><span style="left:25px">Rudy Tallis</span><span style="left:168px">11.13km away</span><span style="left:408px">_</span><span class="badge sent" style="left:559px">Request Sent</span></div>
    <div class="tr" style="top:241px;height:69px;border-bottom:0"><span style="left:25px">Carl Hendry</span><span style="left:165px">11.91km away</span><span style="left:408px">_</span><span class="badge pending" style="left:559px">Pending</span></div>
  </div>
</section>
</body>
</html>
```